real esate business card with company logo and name

we need a business card design for a real esate company

The company name is Walsh & Brand Pty Ltd, and we have our logo designed and will upload. We want classic or moden feel. Black or white background. looks more textured. Should include folowinginformations
Owen Walsh and Lucy Brand
Sales Agents & Onsite Manager
p: 07 5948 2063
F: 07 5948 2174
M:0431 857 219
3/42 Marlow Crescent, FERNLEA QLD 4213

We want this business card looks professonal. Thank you in advance.

Industry/Entity Type

Real Estate Agent

Contact Information for Business Card

Owen Walsh and Lucy Brand
Onsite Manager & Sales Agents
p: 07 5948 2063
M:0431 857 219

Font styles to use
Serif

Colors
000000
fbfbfb
333333
959595

Requirements
Must have
• company logo and name, black or white back ground

```html
<!DOCTYPE html>
<html lang="en">
<head>
<meta charset="utf-8">
<title>Walsh &amp; Brand Pty Ltd — Business Card</title>
<link href="https://fonts.googleapis.com/css2?family=Oswald:wght@400;500&family=Open+Sans:wght@400;600;700&display=swap" rel="stylesheet">
<style>
  :root {
    --page-bg: #2b2725;
    --card-front: #1c1c1c;
    --card-back: #6e6e6e;
    --ink-white: #fbfbfb;
    --ink-grey: #959595;
    --ink-dark: #333333;
    --divider: #3a3a3a;
    --mark: #8a8a8a;
  }
  * { box-sizing: border-box; margin: 0; padding: 0; }
  html, body {
    width: 1200px; height: 844px; overflow: hidden;
    background: var(--page-bg);
  }
  .stage {
    position: relative; width: 1200px; height: 844px;
    display: flex; align-items: center; justify-content: center; gap: 40px;
  }
  .card {
    position: relative; width: 520px; height: 300px;
    box-shadow: 0 18px 40px rgba(0,0,0,.45);
  }
  .card--front {
    background: radial-gradient(ellipse at 70% 30%, #262626 0%, var(--card-front) 70%);
    display: flex;
  }
  .brand-block {
    width: 250px; display: flex; flex-direction: column;
    align-items: center; justify-content: center; gap: 22px;
  }
  .brand-square {
    width: 96px; height: 96px; background: var(--mark);
  }
  .brand-name {
    font-family: "Oswald", sans-serif; font-weight: 400;
    font-size: 22px; letter-spacing: .5px; color: var(--ink-grey);
    text-transform: uppercase;
  }
  .divider {
    width: 1px; margin: 48px 0; background: var(--divider);
  }
  .contact-block {
    flex: 1; padding: 48px 0 0 26px;
    font-family: "Open Sans", sans-serif; color: var(--ink-white);
  }
  .contact-names {
    font-weight: 700; font-size: 15px; color: var(--ink-grey);
  }
  .contact-role { font-size: 12px; margin-top: 2px; }
  .contact-lines { margin-top: 30px; font-size: 12px; line-height: 1.55; }
  .contact-line { display: flex; align-items: center; gap: 10px; }
  .contact-line svg { width: 11px; height: 11px; fill: var(--ink-grey); }
  .contact-address { margin-top: 22px; padding-left: 21px; font-size: 12px; line-height: 1.55; }
  .card--back { background: var(--card-back); }
  .back-name {
    position: absolute; right: 34px; bottom: 74px;
    font-family: "Oswald", sans-serif; font-weight: 400;
    font-size: 26px; letter-spacing: .5px; color: var(--ink-white);
    text-transform: uppercase;
  }
</style>
</head>
<body>
<main class="stage">
  <section class="card card--front">
    <div class="brand-block">
      <div class="brand-square"></div>
      <div class="brand-name">Walsh &amp; Brand Pty Ltd.</div>
    </div>
    <div class="divider"></div>
    <div class="contact-block">
      <p class="contact-names">Owen Walsh and Lucy Brand</p>
      <p class="contact-role">Onsite Manager &amp; Sales Agents</p>
      <div class="contact-lines">
        <p class="contact-line">
          <svg viewBox="0 0 12 12" aria-hidden="true"><path d="M1 4c0-2 2-3 5-3s5 1 5 3l-2 1-1-1.5H4L3 5zM3 6h6l1 5H2z"/></svg>
          07 5948 2063
        </p>
        <p class="contact-line">
          <svg viewBox="0 0 12 12" aria-hidden="true"><path d="M3.5 0h5a1 1 0 0 1 1 1v10a1 1 0 0 1-1 1h-5a1 1 0 0 1-1-1V1a1 1 0 0 1 1-1zm.5 1.5v8h4v-8z"/></svg>
          0431 857 219
        </p>
      </div>
      <p class="contact-address">3/42 Marlow Crescent,<br>FERNLEA QLD 4213</p>
    </div>
  </section>
  <section class="card card--back">
    <div class="back-name">Walsh &amp; Brand Pty Ltd.</div>
  </section>
</main>
</body>
</html>
```